Verodex business card

Business card for sustainable investment company called "Verodex". Verodex is an exchange platform selling carbon credits between buyers and sellers. Carbon Credits are an environmental commodity for reducing global carbon emissions.

the card should obviously have our logo and the theme should be sustainability/environment mixed with a trading platform.

Contact Information for Business Card

Logo, Name, Title, Phone, Email

Colors
0054AA
0677BA
7BADD7
CADEEF
E8F1F8
0094D4
00A9DD
6FCCEA
C7EBF8
E9F6FB
00AB8E
00BBA5
67D7C9
C6EFE9
E9F9F6
59FF00
82FF00
B8FF75
E3FFCB
F4FFEA

```html
<!DOCTYPE html>
<html lang="en">
<head>
<meta charset="utf-8">
<title>Verodex business card</title>
<link href="https://fonts.googleapis.com/css2?family=Montserrat:wght@400;500;700&display=swap" rel="stylesheet">
<style>
  :root {
    --backdrop: #9b9b9b;
    --navy-deep: #101f42;
    --navy: #1b3468;
    --navy-light: #2b4a86;
    --ink: #1d2b48;
    --ink-soft: #5a5f69;
    --sky: #00a9dd;
    --band-start: #5cc6e0;
    --band-end: #4a86c8;
    --white: #ffffff;
  }
  * { margin: 0; padding: 0; box-sizing: border-box; }
  html, body { width: 1200px; height: 588px; overflow: hidden; }
  body {
    background: var(--backdrop);
    font-family: "Montserrat", sans-serif;
    position: relative;
  }
  .card {
    position: absolute;
    width: 487px;
    height: 287px;
    overflow: hidden;
  }
  /* Back side */
  .card-back { left: 87px; top: 141px; }
  .card-back .pattern-field {
    position: absolute; inset: 0;
    background: linear-gradient(125deg, var(--navy-deep) 0%, var(--navy) 50%, var(--navy-light) 100%);
  }
  .card-back .brand {
    position: absolute; left: 247px; top: 196px;
    display: flex; align-items: center; gap: 23px;
  }
  .brand-dot {
    width: 42px; height: 42px; border-radius: 50%;
    background: var(--sky);
    flex: none;
  }
  .card-back .brand-name {
    font-weight: 500; font-size: 31px; color: var(--white);
    letter-spacing: 0.5px;
  }
  /* Front side */
  .card-front { left: 622px; top: 143px; background: var(--white); }
  .card-front .brand {
    position: absolute; left: 29px; top: 124px;
    display: flex; align-items: center; gap: 26px;
  }
  .card-front .brand-name {
    font-weight: 500; font-size: 31px; color: var(--ink);
    letter-spacing: 0.5px;
  }
  .divider {
    position: absolute; left: 260px; top: 95px;
    width: 1.5px; height: 97px; background: var(--ink);
  }
  .contact { position: absolute; left: 275px; top: 91px; color: var(--ink); }
  .contact-name { font-weight: 700; font-size: 18px; letter-spacing: 0.3px; line-height: 22px; }
  .contact-title { font-size: 12.5px; color: var(--ink-soft); line-height: 18px; margin-bottom: 8px; }
  .contact-list { list-style: none; }
  .contact-list li {
    display: flex; align-items: center; gap: 5px;
    font-size: 12.5px; line-height: 18px; color: var(--ink-soft);
  }
  .contact-list svg { width: 11px; height: 11px; flex: none; }
  .accent-band {
    position: absolute; left: 0; bottom: 0; width: 100%; height: 11px;
    background: linear-gradient(90deg, var(--band-start), var(--band-end));
  }
</style>
</head>
<body>
  <section class="card card-back">
    <div class="pattern-field" role="img" aria-label="Repeating brand emblem pattern in shades of navy blue"></div>
    <div class="brand">
      <span class="brand-dot"></span>
      <span class="brand-name">VERODEX</span>
    </div>
  </section>

  <section class="card card-front">
    <div class="brand">
      <span class="brand-dot"></span>
      <span class="brand-name">VERODEX</span>
    </div>
    <div class="divider"></div>
    <div class="contact">
      <p class="contact-name">MARCUS TRENT</p>
      <p class="contact-title">President</p>
      <ul class="contact-list">
        <li>
          <svg viewBox="0 0 24 24" aria-hidden="true"><path fill="#2f7fc4" d="M6.6 10.8a15.1 15.1 0 0 0 6.6 6.6l2.2-2.2a1 1 0 0 1 1-.25 11.4 11.4 0 0 0 3.6.57 1 1 0 0 1 1 1V20a1 1 0 0 1-1 1A17 17 0 0 1 3 4a1 1 0 0 1 1-1h3.5a1 1 0 0 1 1 1c0 1.25.2 2.45.57 3.57a1 1 0 0 1-.25 1z"/></svg>
          555-018-2374
        </li>
        <li>
          <svg viewBox="0 0 24 24" aria-hidden="true"><rect x="2" y="5" width="20" height="14" rx="1.5" fill="#2f7fc4"/><path d="M2.5 6l9.5 7 9.5-7" stroke="#fff" stroke-width="1.6" fill="none"/></svg>
          marcus.trent@verodex.com
        </li>
        <li>
          <svg viewBox="0 0 24 24" aria-hidden="true"><circle cx="12" cy="12" r="10" fill="#2f7fc4"/><path d="M2 12h20M12 2c3 3 3 17 0 20M12 2c-3 3-3 17 0 20" stroke="#fff" stroke-width="1.3" fill="none"/></svg>
          www.verodex.com
        </li>
      </ul>
    </div>
    <div class="accent-band"></div>
  </section>
</body>
</html>
```